Basic business card

use my newly created logo - and the phrases (Lower Cost of Test & Accelarated New Product Introduction) - and my new email domain / ID - use at conferences / tradeshows

Industry/Entity Type

semiconductor

Contact Information for Business Card

Daniel K Forde, Owner, communicate via Logo - Lower COT - Cost of Test, Accelerated NPI - New Product Introduction, phone +1 555 613 0946, Chandler, Arizona, USA, daniel.forde@qal-vub.com

Font styles to use
Sans Serif

Requirements
Nice to have
• re-use my logo created via Pixel Harbor last August (#7315926)

```html
<!DOCTYPE html>
<html lang="en">
<head>
<meta charset="utf-8">
<title>QAL-VUB Business Card</title>
<link rel="stylesheet" href="https://fonts.googleapis.com/css2?family=Open+Sans:wght@400;600;700&display=swap">
<style>
  :root {
    --stage: #232323;
    --card: #1e1f24;
    --green: #7bc443;
    --orange: #f39a1f;
    --slate: #4f5a78;
    --white: #f4f4f4;
    --panel: #2a2f38;
    --emboss: #141418;
  }
  * { margin: 0; padding: 0; box-sizing: border-box; }
  html, body {
    width: 1200px; height: 780px; overflow: hidden;
    background: var(--stage);
    font-family: "Open Sans", Arial, sans-serif;
  }
  .canvas {
    position: relative; width: 1200px; height: 780px;
    display: flex; flex-direction: column; align-items: center; justify-content: center; gap: 40px;
  }
  .card {
    position: relative; width: 600px; height: 343px;
    background: var(--card);
    border-radius: 18px;
    overflow: hidden;
    box-shadow: 0 0 0 3px var(--green), 0 10px 30px rgba(0,0,0,.5);
  }
  /* Back side */
  .card--back .brand {
    position: absolute; inset: 0;
    display: flex; align-items: center; justify-content: center; gap: 16px;
  }
  .card--back .brand-mark {
    width: 38px; height: 38px; background: var(--emboss);
  }
  .card--back .brand-name {
    font-size: 64px; font-weight: 600; letter-spacing: 2px; color: var(--emboss);
  }
  /* Front side */
  .card--front .brand {
    position: absolute; left: 34px; top: 28px;
    display: flex; align-items: center; gap: 12px;
  }
  .card--front .brand-mark { width: 30px; height: 30px; background: var(--slate); }
  .card--front .brand-name {
    font-size: 38px; font-weight: 600; letter-spacing: 1px; color: var(--slate); line-height: 1;
  }
  .card-bands { position: absolute; inset: 0; }
  .person {
    position: absolute; left: 34px; top: 142px;
    padding-left: 18px; border-left: 8px solid var(--green);
  }
  .person-name { font-size: 30px; font-weight: 700; line-height: 1.05; }
  .person-name .first { color: var(--green); }
  .person-name .last { color: var(--orange); }
  .person-role { font-size: 15px; font-weight: 600; color: var(--white); margin-top: 4px; }
  .contacts {
    position: absolute; left: 60px; top: 224px;
    list-style: none; display: flex; flex-direction: column; gap: 4px;
  }
  .contacts li {
    display: flex; align-items: center; gap: 10px;
    font-size: 15px; color: var(--white);
  }
  .contacts svg { width: 16px; height: 16px; flex: none; }
  .address {
    position: absolute; right: 22px; top: 210px;
    background: var(--panel);
    padding: 12px 16px;
    font-size: 14px; line-height: 1.45; color: var(--white); text-align: right;
  }
</style>
</head>
<body>
<main class="canvas">

  <section class="card card--back" aria-label="Card back">
    <div class="brand">
      <span class="brand-mark"></span>
      <span class="brand-name">QAL-VUB</span>
    </div>
  </section>

  <section class="card card--front" aria-label="Card front">
    <svg class="card-bands" viewBox="0 0 600 343" aria-hidden="true">
      <polygon points="0,316 360,316 440,290 600,290 600,343 0,343" fill="var(--green)"/>
      <polygon points="0,324 378,324 396,343 0,343" fill="var(--orange)"/>
    </svg>

    <div class="brand">
      <span class="brand-mark"></span>
      <span class="brand-name">QAL-VUB</span>
    </div>

    <div class="person">
      <p class="person-name"><span class="first">Lena</span> <span class="last">Marsh</span></p>
      <p class="person-role">Managing Director</p>
    </div>

    <ul class="contacts">
      <li>
        <svg viewBox="0 0 24 24"><path fill="var(--green)" d="M6.6 10.8a15 15 0 0 0 6.6 6.6l2.2-2.2c.3-.3.7-.4 1-.2 1.1.4 2.3.6 3.6.6.6 0 1 .4 1 1V20c0 .6-.4 1-1 1A17 17 0 0 1 3 4c0-.6.4-1 1-1h3.5c.6 0 1 .4 1 1 0 1.3.2 2.5.6 3.6.1.3 0 .7-.2 1z"/></svg>
        (555) 214-0387
      </li>
      <li>
        <svg viewBox="0 0 24 24"><rect x="2" y="5" width="20" height="14" rx="2" fill="var(--green)"/><path d="M3 6l9 7 9-7" fill="none" stroke="var(--card)" stroke-width="2"/></svg>
        info@qal-vub.com
      </li>
      <li>
        <svg viewBox="0 0 24 24"><circle cx="12" cy="12" r="10" fill="var(--green)"/><path d="M2 12h20M12 2c3 3 3 17 0 20M12 2c-3 3-3 17 0 20" fill="none" stroke="var(--card)" stroke-width="1.5"/></svg>
        www.qal-vub.com
      </li>
    </ul>

    <address class="address">
      48 Cedar Ridge Rd. Suite<br>310 Plano, TX 75001
    </address>
  </section>

</main>
</body>
</html>
```